Stationery Design Task - Stationary, memo and report templates for professional services company

Looking for someone to update stationary design but just as importantly come up with a template for reports and memos for use in our consulting firm. Would also like some brand use guidelines to be able to share with our whole team. We have an existing logo that we like. Need to update with a more contemporary look so that our deliverables to clients look good and professional yet stylish. This is for business to business communications. No need for envelope design. Important to have design for multiple pages, i.e. first page of a report and then 2nd page. Need to use in MS word documents so must be easy to use and replicate. Don't want something overly complex. Clean, fresh looking is best.

Industry/Entity Type

Information Technology

Font styles to use
Sans Serif

Colors
33a6d7
0792cd
85cae6
cee9f5
cedeed
85abd2
3377b5
0455a3

Requirements
Must have
• Clean look but with a little style or pop. Something that can easily be used in word documents. Need to have page styles that have a first page of a report (not a cover page) and then secondary page.
Nice to have
• - Although the dark blue is our primary color. Might be willing to look at some accent color as well.
Should not have
• Not just our logo on the page with a color bar.

```html
<!DOCTYPE html>
<html lang="en">
<head>
<meta charset="utf-8">
<title>Altura Technology Stationery</title>
<link rel="stylesheet" href="https://fonts.googleapis.com/css2?family=Roboto:wght@400;500;700;900&family=Questrial&display=swap">
<style>
  :root {
    --stage: #666666;
    --brand-blue: #0a78c2;
    --brand-blue-deep: #0463a8;
    --ink: #3d3d3d;
    --ink-soft: #555555;
    --rule: #8a8a8a;
    --paper-top: #f4f4f4;
    --paper-bottom: #c8c8c8;
    --sheet-shadow: rgba(0,0,0,0.35);
  }
  * { box-sizing: border-box; margin: 0; padding: 0; }
  html, body { width: 1200px; height: 578px; overflow: hidden; }
  body { background: var(--stage); position: relative; font-family: "Questrial", sans-serif; color: var(--ink); }

  .sheet {
    position: absolute; top: 53px; width: 338px; height: 474px;
    box-shadow: 0 0 3px var(--sheet-shadow);
    overflow: hidden;
  }
  .sheet--cover { left: 62px; background: linear-gradient(180deg, var(--paper-top) 0%, #e2e2e2 55%, var(--paper-bottom) 100%); }
  .sheet--letter { left: 434px; background: linear-gradient(180deg, #f6f6f6 0%, #dedede 60%, var(--paper-bottom) 100%); }
  .sheet--follow { left: 806px; background: linear-gradient(90deg, #ffffff 0%, #f2f2f2 45%, #e4e4e4 100%); }

  .brand-name {
    font-family: "Roboto", sans-serif; font-weight: 700; color: var(--brand-blue);
    letter-spacing: 0.5px; white-space: nowrap; display: flex; align-items: center;
  }
  .brand-name__dot { width: 0.9em; height: 0.9em; border-radius: 50%; background: var(--brand-blue); margin-right: 0.4em; }

  /* Cover */
  .cover-brand { position: absolute; top: 36px; left: 0; width: 100%; justify-content: center; font-size: 22px; }
  .cover-hexagon { position: absolute; left: 0; top: 0; }
  .cover-title {
    position: absolute; left: 0; width: 100%; top: 190px; text-align: center;
    font-family: "Roboto", sans-serif; font-weight: 700; color: #fff;
    font-size: 31px; line-height: 35px; letter-spacing: 0.3px;
  }
  .cover-subtitle {
    position: absolute; left: 0; width: 100%; top: 264px; text-align: center;
    font-family: "Roboto", sans-serif; font-weight: 500; color: #fff; font-size: 12px;
  }
  .prepared-label {
    position: absolute; left: 0; width: 100%; top: 370px; text-align: center;
    font-family: "Roboto", sans-serif; font-weight: 900; color: var(--brand-blue); font-size: 11px; letter-spacing: 0.4px;
  }
  .prepared-name {
    position: absolute; left: 0; width: 100%; top: 385px; text-align: center;
    font-family: "Roboto", sans-serif; font-weight: 500; color: var(--ink-soft); font-size: 11px;
  }
  .cover-rule { position: absolute; left: 26px; right: 27px; top: 422px; height: 1px; background: var(--rule); }
  .proposal-date { position: absolute; top: 429px; font-family: "Roboto", sans-serif; font-size: 8px; line-height: 10px; color: var(--ink); }
  .proposal-date--issued { left: 26px; }
  .proposal-date--valid { right: 27px; text-align: right; }
  .proposal-date__label { color: var(--brand-blue); display: block; }

  /* Letterhead */
  .letter-brand { position: absolute; top: 40px; left: 30px; font-size: 15px; }
  .letter-address {
    position: absolute; top: 70px; left: 63px; font-size: 5.6px; line-height: 8.4px; text-transform: uppercase; color: var(--ink);
  }
  .letter-contacts { position: absolute; top: 69px; left: 154px; list-style: none; font-size: 5.6px; line-height: 8.4px; text-transform: uppercase; }
  .letter-contacts li { display: flex; align-items: center; }
  .contact-icon {
    width: 7px; height: 7px; border-radius: 50%; background: var(--brand-blue); color: #fff;
    font-size: 4.5px; display: inline-flex; align-items: center; justify-content: center; margin-right: 4px;
    font-family: "Roboto", sans-serif; font-weight: 700;
  }
  .letter-decoration, .follow-decoration {
    position: absolute; border-radius: 50%;
    background: radial-gradient(circle, rgba(200,200,200,0.55) 0%, rgba(210,210,210,0.3) 50%, rgba(220,220,220,0) 72%);
  }
  .letter-decoration { left: 140px; top: 100px; width: 250px; height: 250px; }
  .follow-decoration { left: 40px; top: 90px; width: 300px; height: 300px; }
  .letter-body { position: absolute; left: 30px; top: 133px; width: 292px; }
  .letter-greeting { font-size: 9px; margin-bottom: 17px; }
  .letter-body p.letter-para { font-size: 5.3px; line-height: 7.6px; text-align: justify; margin-bottom: 6px; color: var(--ink); }
  .letter-closing { font-size: 5.3px; margin-top: 11px; }
  .letter-signature {
    position: absolute; left: 30px; top: 380px; width: 62px; height: 26px;
    background: linear-gradient(90deg, rgba(40,70,160,0.18), rgba(40,70,160,0.05));
    border-radius: 4px;
  }
</style>
</head>
<body>

<section class="sheet sheet--cover" aria-label="Report cover">
  <div class="brand-name cover-brand"><span class="brand-name__dot"></span>ALTURA TECHNOLOGY</div>
  <svg class="cover-hexagon" width="338" height="474" viewBox="0 0 338 474" aria-hidden="true">
    <defs>
      <linearGradient id="hexFill" x1="0" y1="0" x2="0" y2="1">
        <stop offset="0" stop-color="#0b7bc4"/>
        <stop offset="1" stop-color="#0463a8"/>
      </linearGradient>
    </defs>
    <polygon points="21,239 80,112 257,112 317,239 257,362 80,362" fill="url(#hexFill)"/>
  </svg>
  <h1 class="cover-title">REPORT<br>TITLE HERE</h1>
  <p class="cover-subtitle">YOUR SUBTITLE HERE</p>
  <p class="prepared-label">REPORT PREPARED BY</p>
  <p class="prepared-name">YOUR NAME HERE</p>
  <div class="cover-rule"></div>
  <p class="proposal-date proposal-date--issued"><span class="proposal-date__label">PROPOSAL ISSUED</span>SEP 19,2018</p>
  <p class="proposal-date proposal-date--valid"><span class="proposal-date__label">PROPOSAL VALID TO</span>SEP 19,2019</p>
</section>

<section class="sheet sheet--letter" aria-label="Letterhead">
  <div class="letter-decoration" role="img" aria-label="Faint brand background decoration"></div>
  <div class="brand-name letter-brand"><span class="brand-name__dot"></span>ALTURA TECHNOLOGY</div>
  <address class="letter-address" style="font-style:normal">
    Altura Technology LLC<br>412 Cedar Row,<br>Portland, Oregon 97201
  </address>
  <ul class="letter-contacts">
    <li><span class="contact-icon">P</span>555 210 4873</li>
    <li><span class="contact-icon">E</span>info@alturatech.com</li>
    <li><span class="contact-icon">W</span>www.alturatech.com</li>
  </ul>
  <div class="letter-body">
    <p class="letter-greeting">Dear Mr. Carver,</p>
    <p class="letter-para">Thank you for the opportunity to review your infrastructure needs. Our team has completed an initial assessment of your current network, storage and support arrangements, and we have outlined the key findings below. We believe several improvements can be made quickly and at modest cost to your operations.</p>
    <p class="letter-para">The enclosed proposal describes a phased plan for upgrading your systems over the coming year. Each phase includes clear milestones, a fixed budget and a named consultant who will remain your single point of contact from start to finish.</p>
    <p class="letter-para">We would also recommend a short workshop with your department leads to confirm priorities before work begins. This helps us align the schedule with your business calendar and ensures that no critical service is interrupted during the transition to the new platform.</p>
    <p class="letter-para">Please review the attached documents at your convenience. We are happy to meet and discuss any questions, and we look forward to working with you.</p>
    <p class="letter-closing">Sincerely,</p>
  </div>
  <div class="letter-signature" role="img" aria-label="Handwritten signature"></div>
</section>

<section class="sheet sheet--follow" aria-label="Continuation page">
  <div class="follow-decoration" role="img" aria-label="Faint brand background decoration"></div>
</section>

</body>
</html>
```